Consultancy Business Card Design

We need a business card design for a new company based in singapore called KestrelOak. KestrelOak a boutique consultancy firm offering broad-based business solutions, from conception to re-invention, for ventures from new start-ups to long-running traditional businesses.
Its 2 main divisions (Food & Beverage Operations and Construction & Project Management) have access to a wide range of networks, knowledge bases, and resources to service its clients across numerous diverse sectors. This includes, and is not limited to, construction, F&B, and retail.
We are a company that combines the ambition, boldness and energy of one in the 20s with the dedication, level-headedness and dependability of one entering its 30s. Bridging the experiences of the old with ideals of the young, we draw on the positives of both to create a unique synergy.
We hope to see designs that fits our company profile.
Industry/Entity Type
Boutique
Contact Information for Business Card
KestrelOak(Company Name)
Marcus Thiel (Name)
Principle Consultant (Title)
F&B and Hospitality (Division)
(+65) 8043 5617 (Contact no.)
marcus@kestreloak.com.sg (Email)
Colors
Designer to choose colors to be used in the design.

```html
<!DOCTYPE html>
<html lang="en">
<head>
<meta charset="utf-8">
<title>KestrelOak Business Card</title>
<link href="https://fonts.googleapis.com/css2?family=Montserrat:wght@300;400;500&display=swap" rel="stylesheet">
<style>
  :root {
    --backdrop: #2a2a2a;
    --red-light: #ef4d4d;
    --red: #e12a2a;
    --red-deep: #cc1d1d;
    --white: #ffffff;
    --ink: #3a3a3a;
    --soft-white: rgba(255,255,255,0.88);
  }
  * { box-sizing: border-box; margin: 0; padding: 0; }
  html, body {
    width: 1200px; height: 900px; overflow: hidden;
    background: var(--backdrop);
    font-family: "Montserrat", sans-serif;
  }
  .stage {
    width: 1200px; height: 900px;
    display: flex; flex-direction: column;
    align-items: center; justify-content: center; gap: 40px;
  }
  .card {
    position: relative;
    width: 720px; height: 410px;
    background: radial-gradient(ellipse at 50% 40%, var(--red-light) 0%, var(--red) 55%, var(--red-deep) 100%);
    box-shadow: 0 6px 18px rgba(0,0,0,0.35);
  }
  .wordmark {
    position: absolute; left: 50%; transform: translateX(-50%);
    background: var(--white);
    padding: 14px 30px;
    color: var(--ink);
    font-weight: 500;
    font-size: 46px;
    letter-spacing: 0.5px;
    line-height: 1;
    white-space: nowrap;
  }
  .card--front .wordmark { top: 110px; }
  .card--back .wordmark { top: 50%; transform: translate(-50%, -50%); }
  .contact-row {
    position: absolute; left: 40px; right: 40px; bottom: 38px;
    display: flex; justify-content: space-between; align-items: flex-start;
  }
  .contact-item {
    width: 33%;
    display: flex; flex-direction: column; align-items: center; gap: 12px;
    color: var(--soft-white);
    font-weight: 300;
    font-size: 13px;
    line-height: 1.45;
    text-align: center;
  }
  .contact-icon { width: 30px; height: 30px; display: block; }
</style>
</head>
<body>
<main class="stage">
  <section class="card card--front">
    <div class="wordmark">KestrelOak</div>
    <div class="contact-row">
      <div class="contact-item">
        <svg class="contact-icon" viewBox="0 0 30 30" aria-hidden="true">
          <rect x="1" y="1" width="28" height="28" fill="none" stroke="#fff" stroke-width="1.5"/>
          <circle cx="15" cy="12" r="3.6" fill="#fff"/>
          <path d="M8.5 21.5c0-3.6 2.9-5.5 6.5-5.5s6.5 1.9 6.5 5.5z" fill="#fff"/>
        </svg>
        <p class="contact-text">Marcus Thiel<br>Principle Consultant -<br>F&amp;B and Hospitality</p>
      </div>
      <div class="contact-item">
        <svg class="contact-icon" viewBox="0 0 30 30" aria-hidden="true">
          <rect x="1" y="1" width="28" height="28" fill="none" stroke="#fff" stroke-width="1.5"/>
          <path d="M10.5 8.5l2.6-.6 1.4 3.3-1.7 1.1c.8 1.8 2.1 3.1 3.9 3.9l1.1-1.7 3.3 1.4-.6 2.6c-.2.6-.8 1-1.4.9-5.2-.6-8.9-4.3-9.5-9.5-.1-.6.3-1.2.9-1.4z" fill="#fff"/>
        </svg>
        <p class="contact-text">(+65) 8043 5617</p>
      </div>
      <div class="contact-item">
        <svg class="contact-icon" viewBox="0 0 30 30" aria-hidden="true">
          <rect x="1" y="1" width="28" height="28" fill="none" stroke="#fff" stroke-width="1.5"/>
          <rect x="8" y="10" width="14" height="10" fill="#fff"/>
          <path d="M8 10l7 5.5 7-5.5" fill="none" stroke="#e12a2a" stroke-width="1.2"/>
        </svg>
        <p class="contact-text">marcus@kestreloak.com.sg</p>
      </div>
    </div>
  </section>
  <section class="card card--back">
    <div class="wordmark">KestrelOak</div>
  </section>
</main>
</body>
</html>
```